Graphic Redesign: Front page of web app for nursery schools (PSD)

Redesign the front page of a web tool used by nursery schools for bi-directional communication with parents(PSD File type)

```html
<!DOCTYPE html>
<html lang="fi">
<head>
<meta charset="utf-8">
<title>Lapsikello – Viestintätyökalu Päiväkodeille</title>
<link rel="stylesheet" href="https://fonts.googleapis.com/css2?family=Open+Sans:wght@300;400;600&family=Great+Vibes&display=swap">
<style>
  :root {
    --sky-top: #c9d6ea;
    --sky-mid: #e9eef7;
    --page: #ffffff;
    --ink: #1b1b1b;
    --ink-soft: #555555;
    --tab-bg: #e6e6e6;
    --tab-text: #8a2e2e;
    --tab-active: #3d8fd6;
    --tile-top: #f4fbf1;
    --tile-bottom: #dff1da;
    --tile-border: #b9cdb4;
    --panel-bar: #3a3a3a;
    --panel-strip: #585858;
    --panel-btn: #3c3c3c;
    --panel-btn-border: #6a6a6a;
    --panel-bg: #e9e9e9;
    --card-border: #c9c9c9;
    --green: #3c9a10;
    --footer-text: #777777;
  }
  * { box-sizing: border-box; margin: 0; padding: 0; }
  html, body { width: 1200px; height: 835px; overflow: hidden; }
  body {
    position: relative;
    font-family: "Open Sans", Verdana, sans-serif;
    color: var(--ink);
    background: linear-gradient(to bottom, var(--sky-top) 0px, var(--sky-mid) 90px, var(--page) 170px, var(--page) 100%);
  }
  .brand-name {
    position: absolute; left: 132px; top: 48px;
    font-family: "Open Sans", sans-serif; font-weight: 300;
    font-size: 64px; letter-spacing: -1px; color: var(--ink);
  }
  .tagline {
    position: absolute; right: 82px; top: 94px;
    font-family: "Great Vibes", cursive; font-size: 34px; color: var(--ink);
    text-shadow: 1px 1px 0 #bbb;
  }
  .main-nav { position: absolute; top: 144px; left: 67px; height: 40px; }
  .main-nav a {
    position: absolute; top: 0; height: 38px; line-height: 38px;
    background: var(--tab-bg); color: var(--tab-text);
    font-size: 15px; text-align: center; text-decoration: none;
  }
  .main-nav a.is-active { background: #f3f5f8; border-bottom: 3px solid var(--tab-active); }
  .feature-tiles a {
    position: absolute; top: 201px; height: 63px;
    display: flex; align-items: center; gap: 10px; padding-left: 14px;
    background: linear-gradient(to bottom, var(--tile-top), var(--tile-bottom));
    border: 1px solid var(--tile-border);
    box-shadow: 0 2px 4px rgba(0,0,0,.25);
    color: var(--ink); font-size: 20px; text-decoration: none;
  }
  .feature-tiles svg { flex: none; }
  .panel {
    position: absolute; left: 67px; top: 276px; width: 1057px; height: 391px;
    background: var(--panel-bg); border-top: 5px solid var(--panel-bar);
    box-shadow: 0 4px 10px rgba(0,0,0,.3);
  }
  .panel-nav {
    position: absolute; left: 11px; top: 3px; width: 1035px; height: 50px;
    background: var(--panel-strip);
  }
  .panel-nav a {
    position: absolute; top: 8px; height: 34px;
    display: flex; align-items: center; justify-content: center; text-align: center;
    background: var(--panel-btn); border: 1px solid var(--panel-btn-border);
    color: #fff; font-size: 15px; line-height: 15px; text-decoration: none;
  }
  .offer-card {
    position: absolute; left: 14px; top: 65px; width: 1025px; height: 292px;
    background: #fff; border: 1px solid var(--card-border); border-radius: 6px;
  }
  .offer-col { position: absolute; }
  .offer-col h2 { font-weight: 400; font-size: 21px; line-height: 26px; color: var(--green); }
  .offer-col ul { list-style: none; }
  .offer-col li {
    position: relative; padding-left: 35px;
    font-size: 19px; line-height: 23px;
  }
  .offer-col li svg { position: absolute; left: 0; top: 2px; }
  .site-footer {
    position: absolute; left: 67px; top: 685px; width: 1057px; height: 83px;
    border: 1px solid var(--card-border); text-align: center;
    font-size: 13.5px; color: var(--footer-text); padding-top: 14px; line-height: 20px;
  }
  .site-footer a { color: var(--footer-text); }
</style>
</head>
<body>

<header>
  <div class="brand-name">Lapsikello</div>
  <div class="tagline">Lapsikello Viestintätyökalu Päiväkodeille</div>
</header>

<nav class="main-nav">
  <a class="is-active" style="left:0;width:57px">Koti</a>
  <a style="left:65px;width:83px">Palvelut</a>
  <a style="left:157px;width:122px">Rekisteröinti</a>
  <a style="left:287px;width:195px">Päiväkoti Kirjautuminen</a>
  <a style="left:490px;width:177px">Lasten Kirjautuminen</a>
  <a style="left:676px;width:88px">Teemat</a>
  <a style="left:772px;width:282px;text-align:left;padding-left:14px">Tietoturva</a>
</nav>

<nav class="feature-tiles">
  <a style="left:67px;width:181px">
    <svg width="56" height="46" viewBox="0 0 56 46"><path d="M4 8 L26 12 L26 42 L4 38Z" fill="#fff" stroke="#222" stroke-width="3"/><path d="M52 8 L30 12 L30 42 L52 38Z" fill="#fff" stroke="#222" stroke-width="3"/><path d="M26 12 Q28 8 30 12" fill="none" stroke="#222" stroke-width="3"/><circle cx="46" cy="38" r="6" fill="#c62828"/></svg>
    TARINAT
  </a>
  <a style="left:257px;width:176px">
    <svg width="56" height="46" viewBox="0 0 56 46"><path d="M4 8 L26 12 L26 42 L4 38Z" fill="#fff" stroke="#222" stroke-width="3"/><path d="M52 8 L30 12 L30 42 L52 38Z" fill="#fff" stroke="#222" stroke-width="3"/><path d="M26 12 Q28 8 30 12" fill="none" stroke="#222" stroke-width="3"/><circle cx="46" cy="38" r="6" fill="#2e9e2e"/></svg>
    TARINAT
  </a>
  <a style="left:440px;width:153px">
    <svg width="54" height="34" viewBox="0 0 54 34"><path d="M10 4 H44 Q52 4 52 16 Q52 32 44 30 L36 24 H18 L10 30 Q2 32 2 16 Q2 4 10 4Z" fill="#111"/><rect x="11" y="13" width="10" height="3" fill="#fff"/><rect x="14.5" y="9.5" width="3" height="10" fill="#fff"/><circle cx="38" cy="12" r="2.5" fill="#fff"/><circle cx="42" cy="17" r="2.5" fill="#fff"/></svg>
    PELIT
  </a>
  <a style="left:600px;width:249px">
    <svg width="32" height="44" viewBox="0 0 32 44"><rect x="2" y="2" width="28" height="40" fill="#111"/><rect x="9" y="6" width="14" height="14" fill="#fff"/><rect x="9" y="24" width="14" height="14" fill="#fff"/><g fill="#fff"><rect x="3" y="5" width="4" height="3"/><rect x="3" y="13" width="4" height="3"/><rect x="3" y="21" width="4" height="3"/><rect x="3" y="29" width="4" height="3"/><rect x="3" y="37" width="4" height="3"/><rect x="25" y="5" width="4" height="3"/><rect x="25" y="13" width="4" height="3"/><rect x="25" y="21" width="4" height="3"/><rect x="25" y="29" width="4" height="3"/><rect x="25" y="37" width="4" height="3"/></g></svg>
    ESITTYELY VIDEO
  </a>
  <a style="left:857px;width:263px;padding-left:30px">
    <svg width="44" height="50" viewBox="0 0 44 50"><rect x="4" y="6" width="36" height="42" rx="3" fill="#1f3b5a"/><rect x="8" y="12" width="28" height="32" fill="#fff"/><rect x="14" y="2" width="16" height="8" rx="2" fill="#999" stroke="#333"/><path d="M12 28 L20 36 L34 16" fill="none" stroke="#1f3b5a" stroke-width="4"/></svg>
    Palvelut
  </a>
</nav>

<main class="panel">
  <nav class="panel-nav">
    <a style="left:8px;width:169px">Kirjaudu sisaan<br>Koti</a>
    <a style="left:185px;width:166px">Kirjaudu sisaan<br>Päiväkoti</a>
    <a style="left:359px;width:168px">Rekisteröidy</a>
    <a style="left:536px;width:167px">Yhteystiedot</a>
    <a style="left:712px;width:168px">Kokeile Sivuja</a>
  </nav>

  <section class="offer-card">
    <div class="offer-col" style="left:49px;top:18px;width:460px">
      <h2>Lapsikello tarjoaa:<br>Sähköistä tiedotusta koteihin päiväkodilta</h2>
      <ul>
        <li style="margin-top:13px"><svg width="24" height="24" viewBox="0 0 24 24"><path d="M2 14 L8 21 L22 2" fill="none" stroke="#111" stroke-width="2.5"/></svg>Info päiväkodilta tekstiviestillä (vanhemmat maksavat viestit)</li>
        <li style="margin-top:24px"><svg width="24" height="24" viewBox="0 0 24 24"><path d="M2 14 L8 21 L22 2" fill="none" stroke="#111" stroke-width="2.5"/></svg>Kuukausittaisten touhujen lista</li>
        <li style="margin-top:24px"><svg width="24" height="24" viewBox="0 0 24 24"><path d="M2 14 L8 21 L22 2" fill="none" stroke="#111" stroke-width="2.5"/></svg>Videoita lapsien esityksistä</li>
        <li style="margin-top:24px"><svg width="24" height="24" viewBox="0 0 24 24"><path d="M2 14 L8 21 L22 2" fill="none" stroke="#111" stroke-width="2.5"/></svg>Kuvia lapsien piirustuksista</li>
      </ul>
    </div>
    <div class="offer-col" style="left:598px;top:42px;width:400px">
      <h2>Web-pohjainen sisältö perheille</h2>
      <ul>
        <li style="margin-top:13px"><svg width="24" height="24" viewBox="0 0 24 24"><path d="M2 14 L8 21 L22 2" fill="none" stroke="#111" stroke-width="2.5"/></svg>Lapsi harjoittelee nimen kirjoittamista äänen avulla</li>
        <li style="margin-top:18px"><svg width="24" height="24" viewBox="0 0 24 24"><path d="M2 14 L8 21 L22 2" fill="none" stroke="#111" stroke-width="2.5"/></svg>Äänelliset tarinat ja pelit</li>
        <li style="margin-top:17px"><svg width="24" height="24" viewBox="0 0 24 24"><path d="M2 14 L8 21 L22 2" fill="none" stroke="#111" stroke-width="2.5"/></svg>Mahdollisuus ladata kuvia nettiin</li>
      </ul>
    </div>
  </section>
</main>

<footer class="site-footer">
  Copyright @ 2009 Tupa Web . All rights reserved. <a href="#">Terms of Service</a> - <a href="#">Guidelines</a><br>
  <a href="#">Yhteystiedot </a>
</footer>

</body>
</html>
```